BOLD & MINIMALIST DESIGN NEEDED

We want a very bold but minimalistic business card design that is impactful and utilizes both sides of the business card. Our current logo is included for your use.

We want bold fonts and good use of negative space. We don't want the logo to overpower the design.

Target Market(s)

Professionals who are building new commercial buildings.

Industry/Entity Type

Construction

Contact Information for Business Card

Name, Title, email, office phone, cell phone, website

Font styles to use
Serif
Sans Serif

Requirements
Must have
• Bold design!

```html
<!DOCTYPE html>
<html lang="en">
<head>
<meta charset="utf-8">
<title>Crestline Design + Build – Business Card</title>
<link rel="stylesheet" href="https://fonts.googleapis.com/css2?family=Roboto:wght@400;700;900&display=swap">
<style>
  :root {
    --backdrop: #3a3a3a;
    --card-black: #151515;
    --emboss: #262626;
    --emboss-edge: #333333;
    --card-white: #ffffff;
    --ink: #111111;
    --ink-soft: #333333;
    --accent: #7cc142;
    --rule: #222222;
  }
  * { margin: 0; padding: 0; box-sizing: border-box; }
  html, body {
    width: 1200px;
    height: 694px;
    overflow: hidden;
    background: var(--backdrop);
    font-family: "Roboto", Arial, sans-serif;
  }
  .canvas {
    position: relative;
    width: 1200px;
    height: 694px;
    display: flex;
    align-items: center;
    justify-content: center;
    gap: 40px;
  }
  .card {
    position: relative;
    width: 520px;
    height: 297px;
    border-radius: 22px;
    overflow: hidden;
  }

  /* Back side */
  .card--back {
    background: var(--card-black);
    display: flex;
    align-items: center;
    justify-content: center;
  }
  .card--back .brand { text-align: center; }
  .card--back .brand-name {
    color: var(--emboss);
    text-shadow: 0 1px 0 var(--emboss-edge);
  }
  .card--back .brand-tagline {
    color: var(--emboss);
    border-top-color: var(--emboss-edge);
  }

  /* Brand block */
  .brand-name {
    font-weight: 900;
    font-size: 52px;
    letter-spacing: 1px;
    text-transform: uppercase;
    line-height: 1;
  }
  .brand-tagline {
    display: inline-block;
    margin-top: 6px;
    padding-top: 4px;
    border-top: 1.5px solid var(--rule);
    font-weight: 400;
    font-size: 13px;
    letter-spacing: 9px;
    text-transform: uppercase;
  }

  /* Front side */
  .card--front {
    background: var(--card-white);
    padding: 44px 0 0 48px;
  }
  .card--front .brand-name { color: var(--ink); font-size: 40px; }
  .card--front .brand-tagline { color: var(--ink); font-size: 10px; letter-spacing: 7px; }

  .person { margin-top: 28px; }
  .person-name {
    color: var(--accent);
    font-weight: 700;
    font-size: 24px;
    line-height: 1.1;
  }
  .person-title {
    color: var(--ink-soft);
    font-size: 14px;
    margin-top: 2px;
  }
  .contact-list {
    list-style: none;
    margin-top: 10px;
  }
  .contact-item {
    display: flex;
    align-items: center;
    gap: 10px;
    color: var(--ink-soft);
    font-size: 13px;
    line-height: 19px;
  }
  .contact-icon {
    width: 12px;
    height: 12px;
    flex: none;
    fill: var(--ink);
  }
</style>
</head>
<body>
<main class="canvas">

  <section class="card card--back" aria-label="Card back">
    <div class="brand">
      <div class="brand-name">Crestline</div>
      <div class="brand-tagline">Design + Build</div>
    </div>
  </section>

  <section class="card card--front" aria-label="Card front">
    <div class="brand">
      <div class="brand-name">Crestline</div>
      <div class="brand-tagline">Design + Build</div>
    </div>

    <div class="person">
      <div class="person-name">Daniel Carter</div>
      <div class="person-title">Owner</div>
    </div>

    <ul class="contact-list">
      <li class="contact-item">
        <svg class="contact-icon" viewBox="0 0 24 24" aria-hidden="true"><path d="M6.6 10.8a15 15 0 0 0 6.6 6.6l2.2-2.2a1 1 0 0 1 1-.25 11.4 11.4 0 0 0 3.6.57 1 1 0 0 1 1 1V20a1 1 0 0 1-1 1A17 17 0 0 1 3 4a1 1 0 0 1 1-1h3.5a1 1 0 0 1 1 1c0 1.25.2 2.45.57 3.570a1 1 0 0 1-.25 1z"/></svg>
        055-482 913 270
      </li>
      <li class="contact-item">
        <svg class="contact-icon" viewBox="0 0 24 24" aria-hidden="true"><path d="M2 8c0-3 5-4 10-4s10 1 10 4v2h-5V8H7v2H2z"/><path d="M5 11h14l2 9H3z"/></svg>
        055-482 913 271
      </li>
      <li class="contact-item">
        <svg class="contact-icon" viewBox="0 0 24 24" aria-hidden="true"><path d="M2 5h20v14H2z M4 7v.5l8 5.5 8-5.5V7z" fill-rule="evenodd"/></svg>
        hello@crestlinebuild.com
      </li>
      <li class="contact-item">
        <svg class="contact-icon" viewBox="0 0 24 24" aria-hidden="true"><circle cx="12" cy="12" r="10"/><path d="M7 8c2 0 3 1 3 3s-2 2-2 4l-2 1c-1-2-1-5 1-8zm8-2c2 1 3 3 3 5l-3 1-2-2 1-2z" fill="#fff"/></svg>
        www.crestlinebuild.com
      </li>
    </ul>
  </section>

</main>
</body>
</html>
```